Business Card Design for company

We want new business cards. We'd like something different-- yet still highly professional. Our tagline is Providing leadership, delivering success. Stock photos are ok, as long as they are relevant and look upscale.

Target Market(s)

Architecture/Business Management Consulting/Engineering Consulting

Contact Information for Business Card

dark gray background with pops of blue might be good, but you tell me. You're the designers. Rounded corners might be nice, but again, you tell me.

Font styles to use
Serif
Sans Serif

Colors
3276b5
5c5c5c
9d9d9d
fbfbfb

Requirements
Nice to have
• Something different, but still very professional.

```html
<!DOCTYPE html>
<html lang="en">
<head>
<meta charset="utf-8">
<title>Halden Group — Business Card</title>
<link href="https://fonts.googleapis.com/css2?family=Montserrat:wght@600&family=Work+Sans:wght@400;500&display=swap" rel="stylesheet">
<style>
  :root{
    --stage:#1a1a1a;
    --card:#262626;
    --card-deep:#1f1f1f;
    --blue:#3276b5;
    --grey-dark:#5c5c5c;
    --grey-light:#9d9d9d;
    --white:#fbfbfb;
  }
  *{margin:0;padding:0;box-sizing:border-box}
  html,body{width:1200px;height:900px;overflow:hidden;background:var(--stage)}
  .stage{position:relative;width:1200px;height:900px;display:flex;flex-direction:column;align-items:center;justify-content:center;gap:36px}
  .card{position:relative;width:700px;height:400px;border-radius:6px;background:var(--card);overflow:hidden;box-shadow:0 18px 40px rgba(0,0,0,.55)}

  /* back side */
  .card-back{background:var(--card-deep)}
  .card-back .pattern{position:absolute;inset:0;background:linear-gradient(135deg,#2b2b2b 0%,#1e1e1e 55%,#272727 100%)}
  .card-back .brand-mark{position:absolute;inset:0;display:flex;align-items:center;justify-content:center}
  .card-back .brand-mark span{font-family:"Montserrat",sans-serif;font-weight:600;font-size:40px;letter-spacing:2px;color:var(--white);background:var(--card-deep);padding:6px 18px}

  /* front side */
  .card-front{display:flex;align-items:center}
  .brand{width:330px;padding-left:60px}
  .brand-name{font-family:"Montserrat",sans-serif;font-weight:600;font-size:52px;line-height:1.02;letter-spacing:1px;color:var(--white);text-transform:uppercase}
  .divider{width:2px;height:200px;background:var(--white);opacity:.85;margin:0 40px 0 10px}
  .contact{font-family:"Work Sans",sans-serif;color:var(--white)}
  .contact .name{font-weight:500;font-size:26px;letter-spacing:2px;color:var(--blue);text-transform:uppercase}
  .contact .role{font-size:17px;margin-top:2px;margin-bottom:22px}
  .contact .address{font-size:17px;line-height:1.4;margin-bottom:12px}
  .contact ul{list-style:none}
  .contact li{display:flex;align-items:center;gap:10px;font-size:18px;line-height:1.55}
  .contact li svg{width:12px;height:12px;flex:none}
  .contact .accent{color:var(--blue)}
</style>
</head>
<body>
<main class="stage">
  <section class="card card-back" aria-label="Card back">
    <div class="pattern" role="img" aria-label="Tonal repeating pattern of the company name across the card"></div>
    <div class="brand-mark"><span>HALDEN GROUP</span></div>
  </section>

  <section class="card card-front" aria-label="Card front">
    <div class="brand">
      <p class="brand-name">Halden<br>Group</p>
    </div>
    <div class="divider"></div>
    <div class="contact">
      <p class="name">Daniel Hartley</p>
      <p class="role">Director</p>
      <p class="address">214b Harbour Lane,<br>Riverton, NZ, 8042</p>
      <ul>
        <li>
          <svg viewBox="0 0 12 12" aria-hidden="true"><path d="M2.5 1h2l1 2.5-1.3 1a6 6 0 0 0 3.3 3.3l1-1.3L11 7.5v2a1 1 0 0 1-1 1A9 9 0 0 1 1.5 2a1 1 0 0 1 1-1z" fill="var(--blue)"/></svg>
          (555) 014-2290
        </li>
        <li>
          <svg viewBox="0 0 12 12" aria-hidden="true"><rect x="1" y="2.5" width="10" height="7" fill="none" stroke="var(--blue)" stroke-width="1.2"/><path d="M1 2.5l5 4 5-4" fill="none" stroke="var(--blue)" stroke-width="1.2"/></svg>
          info@haldengroup.com
        </li>
        <li>
          <svg viewBox="0 0 12 12" aria-hidden="true"><circle cx="6" cy="6" r="5" fill="none" stroke="var(--blue)" stroke-width="1.1"/><ellipse cx="6" cy="6" rx="2.2" ry="5" fill="none" stroke="var(--blue)" stroke-width="1"/><path d="M1 6h10" stroke="var(--blue)" stroke-width="1"/></svg>
          <span>www.<span class="accent">haldengroup</span>.com</span>
        </li>
      </ul>
    </div>
  </section>
</main>
</body>
</html>
```